High Tech Real Estate Startup needs a business card

We are developing an innovative real estate marketing product based around advanced search and virtual reality.

We talk to people, we need business cards.

Target Market(s)

The target market is technology professionals and realtors.

Contact Information for Business Card

The information to be included will include

Name
Title
Phone Number
E-mail Address
www.zelquin.com

It should use simple iconography for each one of those fields.

Font styles to use
Other font styles liked:
• Co, Jubilat, Avenir

Colors

Designer to choose colors to be used in the design.

Requirements
Must have
• Clean aesthetic,
• Good use of negative space.
• It should use our company logo, shown in the attached file. It is able to use the negative of that logo (coloured font and white background) and I have attached other acceptable accent colours in a swatch file.
Should not have
• Should not be too busy
• No extraneous text (slogans, tag lines etc)

```html
<!DOCTYPE html>
<html lang="en">
<head>
<meta charset="UTF-8">
<title>Zelquin Business Card</title>
<link href="https://fonts.googleapis.com/css2?family=Open+Sans:wght@400;600&display=swap" rel="stylesheet">
<style>
  :root {
    --backdrop: #3b3b3d;
    --card: #1f1f21;
    --card-edge: #29292b;
    --logo-grey: #4a4a4d;
    --accent: #3fb8c4;
    --text-light: #eeeeee;
    --text-soft: #cfcfcf;
  }
  * { margin: 0; padding: 0; box-sizing: border-box; }
  html, body {
    width: 799px;
    height: 1200px;
    overflow: hidden;
    background: var(--backdrop);
    font-family: "Open Sans", Arial, sans-serif;
  }
  .sheet {
    width: 799px;
    height: 1200px;
    display: flex;
    flex-direction: column;
    justify-content: space-around;
    align-items: center;
  }
  .card {
    width: 560px;
    height: 320px;
    background: var(--card);
    border: 1px solid var(--card-edge);
    border-radius: 26px;
    box-shadow: 0 14px 30px rgba(0, 0, 0, 0.35);
    position: relative;
  }
  .card-front {
    display: flex;
    align-items: center;
    justify-content: center;
  }
  .brand-name {
    font-size: 62px;
    font-weight: 600;
    letter-spacing: 4px;
    color: var(--logo-grey);
  }
  .card-back {
    display: flex;
    align-items: center;
    justify-content: center;
  }
  .contact-block {
    width: 250px;
  }
  .person-name {
    font-size: 24px;
    font-weight: 600;
    color: var(--accent);
    line-height: 1.2;
    white-space: nowrap;
  }
  .divider {
    height: 1px;
    margin: 8px 0 6px;
    background: linear-gradient(90deg, rgba(63,184,196,0.1), var(--accent) 45%, rgba(63,184,196,0.1));
  }
  .person-title {
    font-size: 13px;
    color: var(--text-soft);
    margin-bottom: 18px;
  }
  .contact-list {
    list-style: none;
    font-size: 15px;
    color: var(--text-light);
    line-height: 1.35;
  }
</style>
</head>
<body>
  <main class="sheet">
    <section class="card card-front" aria-label="Card front">
      <span class="brand-name">ZELQUIN</span>
    </section>
    <section class="card card-back" aria-label="Card back">
      <div class="contact-block">
        <p class="person-name">Ellis Marrow Grant</p>
        <div class="divider"></div>
        <p class="person-title">Managing Director</p>
        <ul class="contact-list">
          <li>408.362.1970</li>
          <li>ellis@zelquin.com</li>
          <li>www.zelquin.com</li>
        </ul>
      </div>
    </section>
  </main>
</body>
</html>
```